MIRA FLINT'S Gingerbeer beverages needs a logo design for a our label.

Mira Flint is the name of my ginger beer. the font I would like use for MIRA FLINT is Emperator hand Ess and a script for Ginger beer. the label will be printed on clear vinyl. Its a Extra Spicy from 700 year old recipe. We make it with a wild probiotic. The finial design should create a thirst for great tasting product have a simple image that reflect nature of the ginger planet. Colors can be bright red like maroon and gold. Business is in Texas.

```html
<!DOCTYPE html>
<html lang="en">
<head>
<meta charset="utf-8">
<title>Mira Flint Ginger Beer – Logo and Label</title>
<link href="https://fonts.googleapis.com/css2?family=Cinzel:wght@500&family=Herr+Von+Muellerhoff&family=Playfair+Display:wght@700&display=swap" rel="stylesheet">
<style>
  :root {
    --paper: #ffffff;
    --maroon: #a51c2a;
    --gold: #a8793b;
    --gold-soft: #b59c5e;
    --gold-bright: #e2c25a;
    --sketch-light: #f1e4cc;
    --sketch-mid: #d9b98a;
    --label-tint: #ecebe3;
  }
  html, body {
    margin: 0;
    padding: 0;
    overflow: hidden;
    background: var(--paper);
  }
  .canvas {
    position: relative;
    width: 1200px;
    height: 1200px;
    background: var(--paper);
    overflow: hidden;
  }
  .brand-name {
    font-family: "Cinzel", serif;
    font-weight: 500;
    color: var(--maroon);
    margin: 0;
    white-space: nowrap;
    line-height: 1;
  }
  .brand-script {
    font-family: "Herr Von Muellerhoff", cursive;
    color: var(--gold);
    margin: 0;
    white-space: nowrap;
    line-height: 1;
  }
  .ginger-sketch {
    display: block;
    margin: 0 auto;
  }

  /* Main logo lockup */
  .logo-lockup {
    position: absolute;
    left: 120px;
    top: 144px;
    width: 490px;
    text-align: center;
  }
  .logo-lockup .ginger-sketch { width: 156px; height: 90px; }
  .logo-lockup .brand-name { font-size: 66px; letter-spacing: 1px; margin-top: 12px; }
  .logo-lockup .brand-script { font-size: 78px; margin-top: 2px; }

  /* Flat label */
  .label {
    position: absolute;
    left: 718px;
    top: 545px;
    width: 276px;
    height: 540px;
    background: var(--label-tint);
    border-radius: 6px;
    text-align: center;
    overflow: hidden;
  }
  .label-claims {
    position: absolute;
    left: 0;
    right: 0;
    top: 44px;
    font-family: "Playfair Display", serif;
    font-weight: 700;
    font-size: 13.5px;
    color: var(--gold-soft);
    margin: 0;
  }
  .label-lockup {
    position: absolute;
    left: 0;
    right: 0;
    top: 83px;
  }
  .label-lockup .ginger-sketch { width: 84px; height: 49px; }
  .label-lockup .brand-name { font-size: 32px; margin-top: 8px; }
  .label-lockup .brand-script { font-size: 36px; margin-top: 2px; }
  .label-art {
    position: absolute;
    left: 0;
    top: 237px;
    width: 276px;
    height: 224px;
    display: block;
  }
  .label-volume {
    position: absolute;
    left: 0;
    right: 0;
    bottom: 38px;
    font-family: "Playfair Display", serif;
    font-weight: 700;
    font-size: 16px;
    color: var(--gold-soft);
    margin: 0;
  }
</style>
</head>
<body>
<main class="canvas">
  <section class="logo-lockup">
    <svg class="ginger-sketch" viewBox="0 0 156 90" role="img" aria-label="Sketched ginger root with leaves, brand symbol">
      <defs>
        <linearGradient id="sketch-fill-main" x1="0" y1="0" x2="1" y2="1">
          <stop offset="0" stop-color="var(--sketch-light)"/>
          <stop offset="1" stop-color="var(--sketch-mid)" stop-opacity="0.6"/>
        </linearGradient>
      </defs>
      <rect width="156" height="90" rx="10" fill="url(#sketch-fill-main)"/>
    </svg>
    <h1 class="brand-name">MIRA FLINT</h1>
    <p class="brand-script">Ginger beer</p>
  </section>

  <section class="label">
    <p class="label-claims">Wild Probiotic | Extra Spicy</p>
    <div class="label-lockup">
      <svg class="ginger-sketch" viewBox="0 0 84 49" role="img" aria-label="Small sketched ginger root with leaves, brand symbol">
        <defs>
          <linearGradient id="sketch-fill-label" x1="0" y1="0" x2="1" y2="1">
            <stop offset="0" stop-color="var(--sketch-light)"/>
            <stop offset="1" stop-color="var(--sketch-mid)" stop-opacity="0.6"/>
          </linearGradient>
        </defs>
        <rect width="84" height="49" rx="6" fill="url(#sketch-fill-label)"/>
      </svg>
      <p class="brand-name">MIRA FLINT</p>
      <p class="brand-script">Ginger beer</p>
    </div>
    <svg class="label-art" viewBox="0 0 276 224" role="img" aria-label="Gold line illustration of a ginger root with leaves">
      <defs>
        <linearGradient id="ginger-art-fill" x1="0" y1="0" x2="1" y2="1">
          <stop offset="0" stop-color="var(--gold-bright)" stop-opacity="0.12"/>
          <stop offset="1" stop-color="var(--gold-bright)" stop-opacity="0.38"/>
        </linearGradient>
      </defs>
      <rect width="276" height="224" fill="url(#ginger-art-fill)"/>
    </svg>
    <p class="label-volume">32 fl oz</p>
  </section>
</main>
</body>
</html>
```